New layout on letterheads, businesscards, flyers, brochures etc.

Dear Sir,
We would like to change our layout a bit. We would like to have the same look on everything we make and still keep our logo. We would like some suggestions suitable for a company like ours, where solar systems, heat pumps and LED lighting is reflected. We like our blue colour in our logo (#009ddf) and some of the black reflected in our solar panels and we like the solar cell (almost square with soft corners). We like soft lines, clean look and reflecting expensive solar panels from the very best distributors (QX, Halvorenti, Kestrel Arcwave etc.). We want a light, soft, exclusive and expensive look to it all. We need this for business cards, letterhead/bottom, flyers, brochures and stickers etc.
Thank you in advance.

Tavurn
Lindvej 28 B
8215 Holmsted
Denmark

info@tavurn.dk
www.tavurn.dk

```html
<!DOCTYPE html>
<html lang="en">
<head>
<meta charset="utf-8">
<title>Tavurn Letterhead</title>
<link rel="stylesheet" href="https://fonts.googleapis.com/css2?family=Ubuntu:ital,wght@0,400;0,700;1,400;1,500&display=swap">
<style>
  :root {
    --brand-blue: #1d9ad9;
    --panel-dark: #3b3b3c;
    --logo-grey: #a6a6a6;
    --text-grey: #4a4a4a;
    --label-grey: #333333;
    --paper: #ffffff;
  }
  html, body {
    margin: 0;
    padding: 0;
    overflow: hidden;
    background: var(--paper);
  }
  .letterhead {
    position: relative;
    width: 848px;
    height: 1200px;
    background: var(--paper);
    overflow: hidden;
    font-family: "Ubuntu", sans-serif;
    color: var(--text-grey);
  }
  .edge-band {
    position: absolute;
    left: 0;
    width: 848px;
    display: flex;
  }
  .edge-band--top { top: 0; height: 11px; }
  .edge-band--bottom { bottom: 0; height: 13px; }
  .edge-band__blue { width: 647px; background: var(--brand-blue); }
  .edge-band__dark { flex: 1; background: var(--panel-dark); }

  .brand-mark {
    position: absolute;
    top: 96px;
    right: 79px;
    display: flex;
    align-items: center;
    gap: 12px;
  }
  .brand-mark__cell {
    width: 44px;
    height: 44px;
    border-radius: 10px;
    background: var(--brand-blue);
  }
  .brand-mark__name {
    font-size: 44px;
    font-weight: 700;
    color: var(--logo-grey);
    letter-spacing: 1px;
    line-height: 1;
  }

  .sender {
    position: absolute;
    right: 81px;
    top: 1011px;
    text-align: right;
    font-size: 16px;
    line-height: 21.5px;
  }
  .sender__address { margin: 0 0 19px; font-style: normal; }
  .sender__contact { margin: 0; }
  .sender__label { font-style: italic; color: var(--label-grey); }
  .sender__web {
    font-style: italic;
    font-weight: 500;
    color: var(--brand-blue);
  }
</style>
</head>
<body>
<div class="letterhead">
  <div class="edge-band edge-band--top">
    <div class="edge-band__blue"></div>
    <div class="edge-band__dark"></div>
  </div>

  <div class="brand-mark">
    <div class="brand-mark__cell"></div>
    <div class="brand-mark__name">Tavurn</div>
  </div>

  <div class="sender">
    <address class="sender__address">
      Lindvej 28 B<br>
      8215 Holmsted<br>
      Denmark
    </address>
    <p class="sender__contact">
      <span class="sender__label">Phone :</span> P +45 86 31 52 70<br>
      <span class="sender__label">Email :</span> info@tavurn.dk<br>
      <span class="sender__web">www.tavurn.dk</span>
    </p>
  </div>

  <div class="edge-band edge-band--bottom">
    <div class="edge-band__blue"></div>
    <div class="edge-band__dark"></div>
  </div>
</div>
</body>
</html>
```